Business Card Design

We need a business card designed for our new company. Prefer a black card with white logo & writing.

Contact Information for Business Card

Ted Galloway, address: 7-4812 Fernhollow Road, Abbotsford, BC, V3K 8R2, Office Phone: 604-712-3390, Cell: 604-947-2164, Email: ted@resinworkshub.ca

Colors

Designer to choose only greyscale colors for use in the design.

```html
<!DOCTYPE html>
<html lang="en">
<head>
<meta charset="utf-8">
<title>Resinworks Hub – Business Card</title>
<link href="https://fonts.googleapis.com/css2?family=Poppins:wght@300;400;600;700&display=swap" rel="stylesheet">
<style>
  :root {
    --backdrop: #202022;
    --card-black: #1d1d1f;
    --card-white: #ffffff;
    --ink-dark: #1a1a1a;
    --ink-light: #f4f4f4;
    --ink-grey: #b9b9bb;
    --icon-fill: #111111;
  }
  * { margin: 0; padding: 0; box-sizing: border-box; }
  html, body {
    width: 1200px; height: 711px; overflow: hidden;
    background: var(--backdrop);
    font-family: "Poppins", sans-serif;
  }
  .stage {
    position: relative; width: 1200px; height: 711px;
    display: flex; align-items: center; justify-content: center; gap: 40px;
  }
  .card {
    position: relative; width: 540px; height: 309px;
    border-radius: 4px; overflow: hidden;
    box-shadow: 0 14px 30px rgba(0,0,0,0.55);
  }

  /* Front */
  .card-front { background: var(--card-black); display: flex; align-items: center; justify-content: center; }
  .brand { display: flex; align-items: center; gap: 14px; }
  .brand-mark { width: 26px; height: 26px; border: 2px solid var(--ink-grey); }
  .brand-name {
    font-weight: 600; font-size: 34px; letter-spacing: 3px;
    color: var(--ink-grey); line-height: 1;
  }

  /* Back */
  .card-back { background: var(--card-black); }
  .back-field { position: absolute; inset: 0; }
  .back-brand {
    position: absolute; left: 26px; top: 140px;
    display: flex; align-items: center; gap: 7px;
  }
  .back-brand .brand-mark { width: 12px; height: 12px; border-width: 1.5px; border-color: var(--ink-light); }
  .back-brand .brand-name { font-size: 13px; letter-spacing: 1px; color: var(--ink-light); }

  .holder { position: absolute; right: 30px; top: 28px; text-align: right; color: var(--ink-light); }
  .holder-name { font-size: 30px; line-height: 1; }
  .holder-first { font-weight: 700; }
  .holder-last { font-weight: 300; }
  .holder-role { font-size: 11px; font-weight: 400; margin-top: 3px; }

  .contact { position: absolute; left: 262px; top: 138px; color: var(--ink-dark); }
  .icon-row { display: flex; gap: 8px; margin-bottom: 6px; }
  .icon {
    width: 20px; height: 20px; border-radius: 50%;
    background: var(--icon-fill); display: flex; align-items: center; justify-content: center;
  }
  .icon svg { width: 11px; height: 11px; }
  .contact-lines { font-size: 12px; line-height: 1.3; font-weight: 400; }
  .address { position: absolute; left: 262px; top: 236px; color: var(--ink-dark); }
  .address .icon { margin-left: 40px; }
  .address-lines { font-size: 12px; line-height: 1.3; margin-top: 6px; }
</style>
</head>
<body>
<main class="stage">
  <section class="card card-front">
    <div class="brand">
      <span class="brand-mark"></span>
      <span class="brand-name">RESINWORKS HUB</span>
    </div>
  </section>

  <section class="card card-back">
    <svg class="back-field" viewBox="0 0 540 309" role="img" aria-label="White mountain range silhouette rising across the card">
      <path d="M108 309 C150 250 200 190 232 130 C240 112 246 102 252 96 C320 104 430 108 540 116 L540 309 Z" fill="#ffffff"/>
    </svg>

    <div class="back-brand">
      <span class="brand-mark"></span>
      <span class="brand-name">RESINWORKS HUB</span>
    </div>

    <div class="holder">
      <div class="holder-name"><span class="holder-first">Ted</span> <span class="holder-last">Galloway</span></div>
      <div class="holder-role">Founder &amp; CEO</div>
    </div>

    <div class="contact">
      <div class="icon-row">
        <span class="icon"><svg viewBox="0 0 24 24"><path fill="#fff" d="M6.6 10.8a15 15 0 0 0 6.6 6.6l2.2-2.2c.3-.3.7-.4 1-.2 1.1.4 2.3.6 3.6.6.6 0 1 .4 1 1V20c0 .6-.4 1-1 1A17 17 0 0 1 3 4c0-.6.4-1 1-1h3.5c.6 0 1 .4 1 1 0 1.3.2 2.5.6 3.6.1.3 0 .7-.2 1z"/></svg></span>
        <span class="icon"><svg viewBox="0 0 24 24"><rect x="6" y="2" width="12" height="20" rx="2" fill="none" stroke="#fff" stroke-width="2"/><circle cx="12" cy="18" r="1.2" fill="#fff"/></svg></span>
        <span class="icon"><svg viewBox="0 0 24 24"><rect x="3" y="5" width="18" height="14" rx="1" fill="none" stroke="#fff" stroke-width="2"/><path d="M3 6l9 7 9-7" fill="none" stroke="#fff" stroke-width="2"/></svg></span>
        <span class="icon"><svg viewBox="0 0 24 24"><circle cx="12" cy="12" r="9" fill="none" stroke="#fff" stroke-width="2"/><path d="M3 12h18M12 3c3 3 3 15 0 18M12 3c-3 3-3 15 0 18" fill="none" stroke="#fff" stroke-width="1.6"/></svg></span>
      </div>
      <div class="contact-lines">
        <div>604-712-3390</div>
        <div>604-947-2164</div>
        <div>www.resinworkshub.ca</div>
        <div>ted@resinworkshub.ca</div>
      </div>
    </div>

    <div class="address">
      <span class="icon"><svg viewBox="0 0 24 24"><path fill="#fff" d="M12 2a7 7 0 0 0-7 7c0 5 7 13 7 13s7-8 7-13a7 7 0 0 0-7-7zm0 9.5A2.5 2.5 0 1 1 12 6.5a2.5 2.5 0 0 1 0 5z"/></svg></span>
      <div class="address-lines">
        <div>7-4812 Fernhollow Road,</div>
        <div>Abbotsford, BC, V3K 8R2.</div>
      </div>
    </div>
  </section>
</main>
</body>
</html>
```